Upmarket Dessert Lounge needs a Business Card Design

We are an upmarket dessert lounge needing a business card to match our image.

We want something that is simple yet beautiful, feminine, classy, sophisticated and elegant. We want it to stand out and don't mind if it is bold.

The design should include our logo and colours of red or maroon with gold highlights. We don't mind if black is used.

Marlow & Quince

Target Market(s)

For those who like to indulge or treat themselves and give in to their temptations on good quality desserts.

Industry/Entity Type

Business

Requirements
Must have
• Must include our logo and our name

Marlow & Quince

M & Q

```html
<!DOCTYPE html>
<html lang="en">
<head>
<meta charset="utf-8">
<title>Marlow &amp; Quince — Business Card</title>
<link href="https://fonts.googleapis.com/css2?family=EB+Garamond:wght@500;600&display=swap" rel="stylesheet">
<style>
  :root {
    --backdrop: #efe6e6;
    --maroon: #6b1d1c;
    --gold: #d8ad78;
    --gold-glow: rgba(216, 173, 120, 0.42);
    --gold-fade: rgba(216, 173, 120, 0);
    --white: #fbf6f0;
  }
  html, body {
    margin: 0;
    padding: 0;
    width: 1200px;
    height: 951px;
    overflow: hidden;
    background: var(--backdrop);
  }
  .canvas {
    position: relative;
    width: 1200px;
    height: 951px;
    font-family: "EB Garamond", Georgia, serif;
  }
  .card {
    position: absolute;
    width: 620px;
    height: 360px;
    border-radius: 26px;
    background: var(--maroon);
    box-shadow: 0 10px 24px rgba(60, 20, 20, 0.25);
    overflow: hidden;
  }
  .card--front { left: 110px; top: 80px; }
  .card--back  { left: 470px; top: 500px; }

  .flourish {
    position: absolute;
    width: 64px;
  }
  .flourish--left {
    left: 0;
    top: 120px;
    bottom: 18px;
    background: radial-gradient(ellipse 100% 50% at 0% 55%, var(--gold-glow), var(--gold-fade) 100%);
  }
  .flourish--right {
    right: 0;
    top: 18px;
    height: 220px;
    background: radial-gradient(ellipse 100% 50% at 100% 45%, var(--gold-glow), var(--gold-fade) 100%);
  }

  .brand-mark {
    position: absolute;
    left: 0;
    right: 0;
    margin: 0;
    text-align: center;
    color: var(--gold);
    font-weight: 600;
  }
  .card--front .brand-mark {
    top: 128px;
    font-size: 44px;
    letter-spacing: 2px;
  }
  .card--back .brand-mark {
    top: 50px;
    font-size: 54px;
    letter-spacing: 1px;
  }

  .web-line {
    position: absolute;
    left: 0;
    right: 0;
    top: 246px;
    margin: 0;
    text-align: center;
    color: var(--white);
    font-size: 21px;
    font-weight: 600;
    letter-spacing: 1px;
  }

  .contact-name {
    position: absolute;
    left: 0;
    right: 0;
    top: 158px;
    margin: 0;
    text-align: center;
    color: var(--gold);
    font-size: 27px;
    font-weight: 600;
  }
  .contact-details {
    position: absolute;
    left: 0;
    right: 0;
    top: 214px;
    text-align: center;
    color: var(--white);
    font-size: 20px;
    font-weight: 500;
    line-height: 1.35;
  }
  .contact-details p { margin: 0; }
  .contact-details .pair span + span { margin-left: 22px; }
</style>
</head>
<body>
<main class="canvas">

  <section class="card card--front" aria-label="Business card front">
    <div class="flourish flourish--left" role="img" aria-label="Gold floral flourish along the left edge"></div>
    <div class="flourish flourish--right" role="img" aria-label="Gold floral flourish along the right edge"></div>
    <h1 class="brand-mark">MARLOW &amp; QUINCE</h1>
    <p class="web-line">www.marlowquince.com</p>
  </section>

  <section class="card card--back" aria-label="Business card back">
    <div class="flourish flourish--left" role="img" aria-label="Gold floral flourish along the left edge"></div>
    <div class="flourish flourish--right" role="img" aria-label="Gold floral flourish along the right edge"></div>
    <p class="brand-mark">M&amp;Q</p>
    <h2 class="contact-name">Marlow &amp; Quince</h2>
    <div class="contact-details">
      <p>212-555-0148</p>
      <p class="pair"><span>info@marlowquince.com</span><span>www.marlowquince.com</span></p>
      <p>14 Orchard Lane, Suite 200, Brookfield 10020</p>
    </div>
  </section>

</main>
</body>
</html>
```